Business card for a new cabinet shop company named Veloran Cabinets for high end cabinets

Design a business card, thinking dark rich green with colours to speak of high end luxury ie; cream, gold, black possibly

Mitchell Tarrowby
Director Craftsman
Email: info@veloranjoinery-example.com.au
Instagram : @veloran.cabinets

```html
<!DOCTYPE html>
<html lang="en">
<head>
<meta charset="utf-8">
<title>Veloran Cabinets — Business Card</title>
<link rel="stylesheet" href="https://fonts.googleapis.com/css2?family=Montserrat:wght@400;500;700&display=swap">
<style>
  :root {
    --backdrop: #9a9a9a;
    --card-green: #063f2b;
    --gold: #c9a965;
    --cream: #f4f1ea;
  }
  * { box-sizing: border-box; margin: 0; padding: 0; }
  html, body {
    width: 1200px;
    height: 1059px;
    overflow: hidden;
    background: var(--backdrop);
    font-family: "Montserrat", Arial, sans-serif;
  }
  .card {
    position: absolute;
    left: 254px;
    width: 698px;
    height: 398px;
    border-radius: 28px;
    background: var(--card-green);
  }
  .card--front { top: 86px; }
  .card--back { top: 570px; }

  .brand-name {
    position: absolute;
    left: 0;
    right: 0;
    text-align: center;
    color: var(--gold);
    font-weight: 500;
    font-size: 50px;
    letter-spacing: 0.5px;
    line-height: 1;
  }
  .card--front .brand-name { top: 92px; }
  .card--back .brand-name { top: 172px; }

  .contact-row {
    position: absolute;
    top: 236px;
    left: 0;
    width: 100%;
    height: 66px;
  }
  .person {
    position: absolute;
    right: calc(100% - 291px);
    top: 0;
    text-align: right;
  }
  .person__name {
    color: var(--gold);
    font-weight: 700;
    font-size: 30px;
    line-height: 1.1;
    white-space: nowrap;
  }
  .person__role {
    color: var(--cream);
    font-size: 17px;
    margin-top: 8px;
    white-space: nowrap;
  }
  .divider {
    position: absolute;
    left: 320px;
    top: 0;
    width: 1px;
    height: 62px;
    background: linear-gradient(to bottom, transparent, var(--gold) 20%, var(--gold) 80%, transparent);
  }
  .details {
    position: absolute;
    left: 344px;
    top: 6px;
    list-style: none;
  }
  .details__item {
    display: flex;
    align-items: center;
    gap: 9px;
    color: var(--cream);
    font-size: 16px;
    height: 20px;
    white-space: nowrap;
  }
  .details__item + .details__item { margin-top: 15px; }
  .details__icon { width: 17px; height: 17px; flex: none; }
  .details__dot {
    width: 14px; height: 14px; flex: none;
    margin: 0 1.5px;
    border-radius: 50%;
    border: 1.6px solid var(--gold);
  }
</style>
</head>
<body>
  <section class="card card--front" aria-label="Card front">
    <p class="brand-name">Veloran Cabinets</p>
    <div class="contact-row">
      <div class="person">
        <p class="person__name">Mitchell Tarrowby</p>
        <p class="person__role">Director Craftsman</p>
      </div>
      <span class="divider"></span>
      <ul class="details">
        <li class="details__item">
          <svg class="details__icon" viewBox="0 0 18 18" aria-hidden="true">
            <rect x="1" y="3.5" width="16" height="11" rx="1" fill="var(--gold)"/>
            <path d="M1.5 4.5 L9 10 L16.5 4.5" fill="none" stroke="var(--card-green)" stroke-width="1.5"/>
          </svg>
          info@veloranjoinery-example.com.au
        </li>
        <li class="details__item">
          <span class="details__dot" aria-hidden="true"></span>
          @veloran.cabinets
        </li>
      </ul>
    </div>
  </section>

  <section class="card card--back" aria-label="Card back">
    <p class="brand-name">Veloran Cabinets</p>
  </section>
</body>
</html>
```